Design the Business card for NetVaultic

Business card required for a professional Cyber Security business.
Company Logo and Icon has already been provided however I would like other options for the logo and icon to compare to. Alternatively, please refine/enhance the image of the logo.icon I have already provided.

If you are going to use the provided logo and icon, I was thinking that the company raised Logo on White background would serve well on the front of the card. See attached. AND, a large company raised stand-alone icon to appear on black background on the back of the card with tagline 'Cyber Risk Management, Governance and Consulting' or 'Cyber Security for your Business' See attached.
Alternatively, provide your own design for the logo and icon.

Target Market(s)

Enterprise, Government, Financial.

Contact Information for Business Card

Tavin Orloweth
Founder and CEO

Email Address
Mobile Number
Website URL
LinkedIn URL

Logo Text

NetVaultic - see attached example of logo

Font styles to use
Other font styles liked:
• Berlin Sans FB

Requirements
Must have
• Clean large and bold icon on the back with tagline.
• Horizontal alignment,
Nice to have
• Round edges.
• Raised Logo/Icon
Should not have
• An unprofessional look and feel.

```html
<!DOCTYPE html>
<html lang="en">
<head>
<meta charset="utf-8">
<title>NetVaultic Business Card</title>
<link rel="stylesheet" href="https://fonts.googleapis.com/css2?family=Ubuntu:wght@400;500&display=swap">
<style>
  :root {
    --backdrop: #2a2a2a;
    --card-front: #f4f4f4;
    --card-back: #1b1c1d;
    --brand-blue: #1a6fba;
    --tag-blue: #4a72cf;
    --accent-yellow: #f0b400;
    --text-grey: #454545;
    --rule-grey: #9a9a9a;
  }
  * { margin: 0; padding: 0; box-sizing: border-box; }
  html, body { width: 1200px; height: 960px; overflow: hidden; }
  body {
    background: var(--backdrop);
    position: relative;
    font-family: "Ubuntu", sans-serif;
  }
  .card {
    position: absolute;
    width: 600px;
    height: 343px;
    box-shadow: 0 4px 10px rgba(0,0,0,0.5);
  }
  .card--front { left: 314px; top: 113px; background: var(--card-front); }
  .card--back { left: 311px; top: 472px; width: 601px; background: var(--card-back); }

  .front__wordmark {
    position: absolute;
    right: 46px;
    top: 106px;
    font-size: 34px;
    font-weight: 500;
    color: var(--brand-blue);
  }
  .front__marker {
    position: absolute;
    left: 0;
    top: 245px;
    width: 18px;
    height: 54px;
    background: var(--brand-blue);
  }
  .front__identity {
    position: absolute;
    left: 53px;
    top: 241px;
    display: flex;
    align-items: baseline;
    gap: 10px;
  }
  .front__name { font-size: 22px; font-weight: 500; color: var(--brand-blue); }
  .front__dash { font-size: 22px; font-weight: 500; color: var(--accent-yellow); }
  .front__role { font-size: 15px; color: var(--accent-yellow); }
  .front__rule {
    position: absolute;
    left: 53px;
    top: 273px;
    width: 504px;
    height: 1px;
    background: var(--rule-grey);
  }
  .contact-row {
    position: absolute;
    left: 53px;
    top: 283px;
    display: flex;
    align-items: center;
    gap: 4px;
    font-size: 13.5px;
    font-weight: 500;
    color: var(--text-grey);
    white-space: nowrap;
  }
  .contact-row__item { display: flex; align-items: center; gap: 3px; }
  .contact-row__icon { width: 13px; height: 13px; flex: none; }

  .back__lockup {
    position: absolute;
    left: 124px;
    top: 118px;
    display: flex;
    align-items: center;
    gap: 10px;
  }
  .back__badge {
    width: 72px;
    height: 72px;
    border-radius: 50%;
    background: var(--tag-blue);
  }
  .back__wordmark {
    font-size: 48px;
    font-weight: 500;
    color: var(--brand-blue);
  }
  .back__tagline {
    position: absolute;
    left: 0;
    right: 0;
    top: 276px;
    text-align: center;
    font-size: 17.5px;
    font-weight: 500;
  }
  .back__tagline-lead { color: var(--tag-blue); }
  .back__tagline-tail { color: var(--accent-yellow); }
</style>
</head>
<body>
  <section class="card card--front">
    <div class="front__wordmark">NetVaultic</div>
    <div class="front__marker"></div>
    <div class="front__identity">
      <span class="front__name">Tavin Orloweth</span>
      <span class="front__dash">-</span>
      <span class="front__role">Founder &amp; CEO</span>
    </div>
    <div class="front__rule"></div>
    <div class="contact-row">
      <span class="contact-row__item">
        <svg class="contact-row__icon" viewBox="0 0 13 13"><rect x="3" y="0.5" width="7" height="12" rx="1.2" fill="#1a6fba"/><rect x="4.2" y="2" width="4.6" height="8" fill="#f4f4f4"/></svg>
        555 210 4863
      </span>
      <span class="contact-row__item">
        <svg class="contact-row__icon" viewBox="0 0 13 13"><rect x="0.5" y="2.5" width="12" height="8" fill="#1a6fba"/><path d="M0.5 2.5 L6.5 7 L12.5 2.5" stroke="#f4f4f4" stroke-width="1" fill="none"/></svg>
        tavin@netvaultic.com
      </span>
      <span class="contact-row__item">
        <svg class="contact-row__icon" viewBox="0 0 13 13"><circle cx="6.5" cy="6.5" r="6" fill="#1a6fba"/><ellipse cx="6.5" cy="6.5" rx="2.4" ry="6" stroke="#f4f4f4" stroke-width="0.8" fill="none"/><line x1="0.5" y1="6.5" x2="12.5" y2="6.5" stroke="#f4f4f4" stroke-width="0.8"/></svg>
        www.netvaultic.com
      </span>
      <span class="contact-row__item">
        <svg class="contact-row__icon" viewBox="0 0 13 13"><circle cx="6.5" cy="6.5" r="6" fill="#1a6fba"/></svg>
        netvaultic
      </span>
    </div>
  </section>

  <section class="card card--back">
    <div class="back__lockup">
      <div class="back__badge"></div>
      <div class="back__wordmark">NetVaultic</div>
    </div>
    <p class="back__tagline">
      <span class="back__tagline-lead">Cyber Risk Management,</span>
      <span class="back__tagline-tail">Governance &amp; Consulting</span>
    </p>
  </section>
</body>
</html>
```